Business card design needed

Family General Practitioner/ Family Physician.
Logo is the logo of the Noble Guild of Family Healers Oceania
http://kpltw.varendo.example/ImageShelf/marks/pages/NGFHO%20mark_jpg.htm
Updates

Project Deadline Extended
Reason: Just a bit more time to make changes and the weekend for me to look at things closely and to choose. Thanks, Orin

Thanks for all the submissions. So many of them are really works of art. Not one of them are not good. The ones that I am eliminating are the ones that I think are not suitable for me personally only, and because if I don't, it makes it very difficult to decide as many of you are also sending me slight variations of a card. I have just decided to choose a second place card too. Can't thank you all enough. Good luck, Orin. P.S - Working today till 10 pm as the card says :-), so probably won't be able to give a feedback till late Saturday night or Sunday morning here in Sydney, Australia. 

Project Deadline Extended
Reason: Just added a second place to the budget and realised that Australia is ahead of the rest of the world in the time zone (only :-) - don't want to offend anyone or start a debate!! ) , so Monday deadline will mean it will be a weekend for the rest of the world. Just wanted to give everyone more time to submit their best, especially since I will be picking a second card too. Can't thank everyone enough for the submissions. P.S - Not keen on photos on the card.

Industry/Entity Type

Business

Contact Information for Business Card

Dr. Orin Halvey M.B.B.S., F.N.G.F.H.O
Family General Practitioner
Address, timings, phone and fax number on the back.

Requirements
Must have
• Timings
Mon 7 am - 7 pm
Tues 7 am - 12 pm
Wed 7 am - 10 pm
Thurs 7 am - 12 pm
Fri 7 am - 8 pm
Sat 8 am - 10 pm
Sun - Off

```html
<!DOCTYPE html>
<html lang="en">
<head>
<meta charset="utf-8">
<title>Family GP Business Card</title>
<link rel="stylesheet" href="https://fonts.googleapis.com/css2?family=Jost:ital,wght@0,400;0,500;0,600;1,500&family=Marcellus&family=Marcellus+SC&family=Roboto+Condensed:wght@700&display=swap">
<style>
  :root {
    --navy: #2e3192;
    --wave: #a5dde3;
    --ink: #2b2b2b;
    --rule: #8a8f99;
    --paper: #ffffff;
    --stage: #e8e4df;
    --label: #2a2a2a;
    --tint-a: #d6e4f3;
    --tint-b: #b9d1ec;
    --photo-a: #f3f6fa;
    --photo-b: #e9e2dc;
  }
  * { box-sizing: border-box; margin: 0; padding: 0; }
  html, body { width: 1200px; height: 788px; overflow: hidden; }
  body {
    position: relative;
    background: var(--stage);
    font-family: "Jost", sans-serif;
    color: var(--ink);
  }
  .side-label {
    position: absolute;
    font-family: "Jost", sans-serif;
    font-size: 21px;
    color: var(--label);
    transform: translateX(-50%);
  }
  .card {
    position: absolute;
    width: 525px;
    height: 300px;
    border-radius: 18px;
    overflow: hidden;
    background: var(--paper);
  }

  /* Front */
  .card-front { left: 338px; top: 72px; }
  .front-wave { position: absolute; left: 0; top: 0; }
  .front-title {
    position: absolute; right: 28px; top: 26px;
    text-align: right; color: #fff;
    font-family: "Marcellus SC", serif; font-size: 15px; line-height: 18px;
    letter-spacing: 0.5px;
  }
  .guild-mark {
    position: absolute; left: 17px; top: 128px; width: 84px;
    display: flex; flex-direction: column; align-items: center; gap: 5px;
    color: var(--navy); font-family: "Jost", sans-serif; font-weight: 500;
    font-size: 10px; line-height: 12px; text-align: center;
  }
  .guild-mark .dot { width: 22px; height: 22px; border-radius: 50%; background: var(--navy); }
  .doctor-name {
    position: absolute; left: 117px; top: 112px;
    font-family: "Jost", sans-serif; font-weight: 600; font-size: 28px;
    color: var(--navy); letter-spacing: 0.3px;
  }
  .credentials {
    position: absolute; left: 117px; top: 148px;
    font-family: "Marcellus", serif; font-size: 21px; color: var(--navy);
    letter-spacing: 2.7px;
  }
  .role {
    position: absolute; left: 117px; top: 181px;
    font-family: "Marcellus SC", serif; font-size: 15.5px; color: var(--navy);
    letter-spacing: 0.9px;
  }
  .address {
    position: absolute; left: 25px; top: 238px;
    font-size: 12.5px; line-height: 16.5px; color: #333; font-style: normal;
  }
  .phones {
    position: absolute; right: 28px; top: 251px;
    font-size: 14px; line-height: 18px; color: #222;
  }
  .phones li { list-style: none; display: flex; align-items: center; justify-content: flex-end; gap: 6px; }
  .phones svg { width: 10px; height: 11px; }

  /* Backs */
  .card-back-photo { left: 54px; top: 446px; }
  .card-back-tint  { left: 622px; top: 446px; background: linear-gradient(100deg, var(--tint-a), var(--tint-b)); }
  .photo-area {
    position: absolute; inset: 0;
    background: radial-gradient(ellipse at 45% 50%, var(--photo-b), var(--photo-a) 70%);
  }
  .back-heading {
    position: absolute; left: 0; right: 0; top: 13px; text-align: center;
    font-family: "Marcellus SC", serif; font-weight: 400; font-size: 21px; letter-spacing: 1.4px; color: #2a2a2a;
  }
  .rule-top, .rule-bottom { position: absolute; left: 0; right: 0; height: 1px; background: var(--rule); }
  .rule-top { top: 52px; }
  .rule-bottom { top: 262px; }
  .rule-mid { position: absolute; left: 264px; top: 52px; width: 1px; height: 210px; background: var(--rule); }
  .timings-title {
    position: absolute; left: 0; width: 264px; top: 62px; text-align: center;
    font-style: italic; font-weight: 500; font-size: 17px; color: #222;
  }
  .timings { position: absolute; left: 43px; top: 85px; }
  .timings li { list-style: none; display: flex; height: 23.4px; font-size: 17px; color: #222; align-items: center; }
  .timings .day { width: 60px; font-weight: 600; }
  .timings .hours { white-space: pre; }
  .appointment { position: absolute; left: 276px; top: 64px; width: 235px; color: #222; font-size: 17px; }
  .appointment h3 { font-weight: 400; font-size: 19px; margin-bottom: 14px; }
  .field { display: flex; align-items: flex-end; height: 26px; }
  .field .fill { flex: 1; border-bottom: 1px solid #333; height: 18px; margin-left: 6px; }
  .field.blank { margin: 12px 0 0 8px; }
  .field.blank .fill { margin-left: 0; }
  .field.gap { margin-top: 14px; }
  .field .unit { margin-left: 6px; }
  .time-fill { flex: 0 0 126px !important; margin-left: 0 !important; }
  .back-note {
    position: absolute; left: 0; right: 0; top: 274px; text-align: center;
    font-family: "Roboto Condensed", sans-serif; font-weight: 700; font-size: 11.5px; color: #333;
  }
</style>
</head>
<body>
  <span class="side-label" style="left:600px; top:32px;">Front</span>
  <span class="side-label" style="left:324px; top:402px;">Back - 2</span>
  <span class="side-label" style="left:896px; top:402px;">Back - 3</span>

  <section class="card card-front">
    <svg class="front-wave" width="525" height="300" viewBox="0 0 525 300" aria-hidden="true">
      <path d="M0,0 H525 V102 C430,114 330,108 230,82 C150,62 70,58 0,70 Z" fill="var(--wave)"/>
      <path d="M0,0 H525 V88 C430,102 330,94 230,68 C150,48 70,40 0,48 Z" fill="var(--navy)"/>
    </svg>
    <p class="front-title">Family General<br>Practitioner</p>
    <div class="guild-mark">
      <span class="dot"></span>
      <span>Noble Guild of Family Healers Oceania</span>
    </div>
    <h1 class="doctor-name">Dr Orin Halvey</h1>
    <p class="credentials">M.B.B.S., F.N.G.F.H.O</p>
    <p class="role">Family General Practitioner</p>
    <address class="address">
      Upper Level, Maple Court<br>
      Ridgeview Arcade Shopping Centre<br>
      Brookvale Heights, NSW 2299
    </address>
    <ul class="phones">
      <li><svg viewBox="0 0 10 11" aria-label="Phone"><rect x="2" y="0" width="6" height="11" rx="1.5" fill="var(--navy)"/><rect x="3.3" y="1.5" width="3.4" height="5" fill="#fff"/></svg>02 5550 2400</li>
      <li><svg viewBox="0 0 10 11" aria-label="Fax"><rect x="2.5" y="0" width="5" height="4" fill="var(--navy)"/><rect x="0" y="4" width="10" height="7" rx="1" fill="var(--navy)"/></svg>02 5550 2233</li>
    </ul>
  </section>

  <section class="card card-back-photo">
    <div class="photo-area" role="img" aria-label="Faint background photo of smiling children lying in a circle"></div>
    <h2 class="back-heading">Caring about your health</h2>
    <div class="rule-top"></div><div class="rule-mid"></div><div class="rule-bottom"></div>
    <p class="timings-title">Clinic Timings</p>
    <ul class="timings">
      <li><span class="day">Mon</span><span class="hours">7 am  -  7 pm</span></li>
      <li><span class="day">Tues</span><span class="hours">7 am  -  12 pm</span></li>
      <li><span class="day">Wed</span><span class="hours">7 am  -  10 pm</span></li>
      <li><span class="day">Thurs</span><span class="hours">7 am  -  12 pm</span></li>
      <li><span class="day">Fri</span><span class="hours">7 am  -  8 pm</span></li>
      <li><span class="day">Sat</span><span class="hours">8 am  -  10 pm</span></li>
      <li><span class="day">Sun</span><span class="hours">Off</span></li>
    </ul>
    <div class="appointment">
      <h3>Your Appointment</h3>
      <div class="field">Name<span class="fill"></span></div>
      <div class="field blank"><span class="fill"></span></div>
      <div class="field gap">Date<span class="fill"></span></div>
      <div class="field gap">time<span class="fill time-fill"></span><span class="unit">am / pm</span></div>
    </div>
    <p class="back-note">24 business hours notice required for cancellations</p>
  </section>

  <section class="card card-back-tint">
    <h2 class="back-heading">Caring about your health</h2>
    <div class="rule-top"></div><div class="rule-mid"></div><div class="rule-bottom"></div>
    <p class="timings-title">Clinic Timings</p>
    <ul class="timings">
      <li><span class="day">Mon</span><span class="hours">7 am  -  7 pm</span></li>
      <li><span class="day">Tues</span><span class="hours">7 am  -  12 pm</span></li>
      <li><span class="day">Wed</span><span class="hours">7 am  -  10 pm</span></li>
      <li><span class="day">Thurs</span><span class="hours">7 am  -  12 pm</span></li>
      <li><span class="day">Fri</span><span class="hours">7 am  -  8 pm</span></li>
      <li><span class="day">Sat</span><span class="hours">8 am  -  10 pm</span></li>
      <li><span class="day">Sun</span><span class="hours">Off</span></li>
    </ul>
    <div class="appointment">
      <h3>Your Appointment</h3>
      <div class="field">Name<span class="fill"></span></div>
      <div class="field blank"><span class="fill"></span></div>
      <div class="field gap">Date<span class="fill"></span></div>
      <div class="field gap">time<span class="fill time-fill"></span><span class="unit">am / pm</span></div>
    </div>
    <p class="back-note">24 business hours notice required for cancellations</p>
  </section>
</body>
</html>
```